Brel Fosk Painting, Eco and Non toxic painting client information brochure.

Brel fosk painting is a painting company that specialises in eco and non toxic paints. This brochure will be left with the client after the initial meeting to explain about my business and hopefully win the job. By reading the text i have provided (see attachment) you can get a better understanding of what we do.
The brochure should be fresh and clean looking, complimenting the Brel Fosk Painting logo and the text provided.
This will be printed onto a recycled paper.
Text and font must clear and easy to read.

Please have a look at my web page. I will be redoing this soon as well but this will give you some ideas of where I'm at.

Would like some picture but not sure what.
I have attached some pics but they don't have to be use
Updates

Hi peeps,

Thanks for all the great designs and sorry i haven't got back to you sooner.
been a bit busy.
Tomorrow i hope to be able to sit down and have a good look at what everybody has done.
Thanks again i really appreciate the effort.

kind regards oswin 

hi designers,

Just sat down and had a good look at the designs sent in and there are some crackers.
Its going to be very difficult to choose. I have only 1 day left before it closes so ill wait till then to see if there are any more submissions come in then ill get back to everybody.
Thanks again for your time and effort.

kind regards oswin 

Hi too all you designers that have worked on my project. 

I am always amazed at all the different designs that come through. Super work guys and girls. 
I have narrowed it down to a couple of designs.
Ill be making the decision tonight.
Thanks again to you all and i really appreciate all the hard work.
I will be doing another brochure in the future for more architecture / builder focus and there were a few designs that would work perfectly for this.

Kinds regards oswin  

Target Market(s)

The work we do is mainly residential repaints, family homes
Mostly I am dealing with the wife of the family or female designers/architects

Industry/Entity Type

Painting

Requirements
Must have
• Company logo, either white or black version what ever suits best.
Text that has been provided.
Brochure will be 1 page A 4, folded into 3 parts both sides.
Front page must have logo and
SPECIALSING IN:
NON TOXIC
ECO FRIENDLY &
HEAT REFLECTIVE PAINTS
Phone 041 382 6190
Painting@brelfosk.biz
www.brelfosk.biz

```html
<!DOCTYPE html>
<html lang="en">
<head>
<meta charset="utf-8">
<title>Brel Fosk Painting – Eco Brochure</title>
<link href="https://fonts.googleapis.com/css2?family=Oswald:wght@400;500;600&family=Open+Sans:wght@400;600&display=swap" rel="stylesheet">
<style>
  :root {
    --backdrop: #e4e2dc;
    --paper: #f3efe2;
    --ink: #3b3935;
    --body-ink: #5a574f;
    --green: #8bb33a;
    --green-deep: #6e9a2a;
    --fold: rgba(0,0,0,0.06);
    --splash-a: #f3c32a;
    --splash-b: #e2397d;
    --splash-c: #37a9d6;
    --splash-d: #8bb33a;
  }
  * { box-sizing: border-box; margin: 0; padding: 0; }
  html, body { width: 849px; height: 1200px; overflow: hidden; }
  body { background: var(--backdrop); font-family: "Open Sans", sans-serif; color: var(--body-ink); position: relative; }

  .sheet {
    position: absolute; left: 24px; width: 801px; height: 540px;
    background: var(--paper); display: flex; overflow: hidden;
    box-shadow: 0 2px 8px rgba(0,0,0,0.12);
  }
  .sheet--front { top: 48px; }
  .sheet--back { top: 620px; }

  .panel { position: relative; width: 267px; height: 100%; padding: 34px 24px 20px; }
  .panel + .panel { border-left: 1px solid var(--fold); }

  .heading {
    font-family: "Oswald", sans-serif; font-weight: 500; color: var(--ink);
    text-transform: uppercase; line-height: 1; letter-spacing: 0.5px;
  }
  .heading--xl { font-size: 40px; margin-bottom: 16px; }
  .heading--vocs { font-size: 30px; margin-bottom: 14px; }
  .heading--vocs span { color: var(--green); }

  .body-copy { font-size: 8.5px; line-height: 1.55; margin-bottom: 9px; }

  .art {
    position: absolute; border-radius: 4px;
  }
  .art--brush {
    left: 40px; top: 330px; width: 190px; height: 170px; border-radius: 50%;
    background: radial-gradient(circle at 50% 45%, rgba(139,179,58,0.55), rgba(226,57,125,0.35) 45%, rgba(55,169,214,0.25) 65%, transparent 75%);
  }
  .art--splash-top {
    left: 0; top: 0; width: 267px; height: 120px; border-radius: 0;
    background: linear-gradient(180deg, rgba(243,195,42,0.55), rgba(226,57,125,0.35) 55%, transparent);
  }
  .art--splash-mid {
    left: 10px; top: 270px; width: 250px; height: 150px; border-radius: 50%;
    background: radial-gradient(ellipse at 55% 50%, rgba(55,169,214,0.5), rgba(139,179,58,0.45) 40%, rgba(243,195,42,0.3) 60%, transparent 75%);
  }
  .art--drips {
    position: absolute; left: 0; top: 0; width: 801px; height: 70px; border-radius: 0;
    background: linear-gradient(90deg, var(--splash-b), var(--splash-a) 25%, var(--splash-d) 50%, var(--splash-c) 75%, var(--splash-b));
    opacity: 0.75;
  }
  .art--house {
    left: 300px; top: 270px; width: 470px; height: 250px; border-radius: 40%;
    background: radial-gradient(ellipse at 50% 50%, rgba(110,154,42,0.75), rgba(139,179,58,0.5) 45%, rgba(200,220,120,0.25) 65%, transparent 78%);
  }

  .cover { text-align: right; padding-top: 128px; }
  .brand {
    display: inline-flex; align-items: center; gap: 6px;
    font-family: "Oswald", sans-serif; font-weight: 500; font-size: 17px;
    color: var(--green-deep); text-transform: uppercase; margin-bottom: 18px;
  }
  .brand__mark { width: 10px; height: 10px; border-radius: 50%; background: var(--green-deep); }
  .specialise { font-family: "Oswald", sans-serif; text-transform: uppercase; line-height: 1; }
  .specialise__intro { font-size: 22px; color: var(--ink); font-weight: 500; }
  .specialise__main { font-size: 31px; color: var(--green); font-weight: 500; }
  .specialise__sub { font-size: 13px; color: var(--green); font-weight: 500; margin-top: 2px; }
  .contact { position: absolute; left: 24px; right: 24px; bottom: 24px; }
  .contact__web { font-family: "Oswald", sans-serif; font-size: 15px; color: var(--ink); margin-bottom: 8px; }
  .contact__lines { font-size: 8px; color: var(--body-ink); }

  .sheet--back .panel { padding-top: 92px; }
</style>
</head>
<body>

<section class="sheet sheet--front">
  <div class="panel panel--vocs">
    <h2 class="heading heading--vocs">VOCs=<br><span>Volatile<br>Organic<br>Compounds</span></h2>
    <p class="body-copy">VOCs are harmful chemicals that are released from many paints into the air you breathe. They continue to be released long after application, lingering in the home for years and affecting the comfort of your family.</p>
    <p class="body-copy">Some of these chemicals are linked to headaches, allergies and breathing problems, and they add to smog and pollution outdoors. Choosing low and zero VOC products reduces these risks for everyone living in the house.</p>
    <p class="body-copy">At Brel Fosk Painting we choose only the safest products and work methods, so your rooms can be lived in straight away and the finish stays fresh, clean and healthy.</p>
  </div>

  <div class="panel panel--owner">
    <h2 class="heading heading--xl">About<br>the owner</h2>
    <p class="body-copy">Brel Fosk has been painting for over 30 years. He is an accredited Green Painter and is often called upon by architects and builders to provide advice on sustainable products and methods.</p>
    <div class="art art--brush" role="img" aria-label="Paint brush with colourful paint splashes"></div>
  </div>

  <div class="panel panel--cover cover">
    <div class="art art--splash-top" role="img" aria-label="Bright paint splashes in yellow, pink and green"></div>
    <div class="brand"><span class="brand__mark"></span>Brel Fosk Painting</div>
    <div class="specialise">
      <div class="specialise__intro">Specialising in:</div>
      <div class="specialise__main">Non toxic</div>
      <div class="specialise__main">Eco friendly</div>
      <div class="specialise__sub">&amp; heat reflective paints</div>
    </div>
    <div class="art art--splash-mid" role="img" aria-label="Colourful paint splashes in blue, green and yellow"></div>
    <div class="contact">
      <div class="contact__web">www.brelfosk.biz</div>
      <div class="contact__lines">Phone 041 382 6190 &nbsp;|&nbsp; Painting@brelfosk.biz</div>
    </div>
  </div>
</section>

<section class="sheet sheet--back">
  <div class="art art--drips" role="img" aria-label="Band of dripping paint in pink, yellow, green and blue"></div>
  <div class="art art--house" role="img" aria-label="Green watercolour house surrounded by leaves"></div>

  <div class="panel panel--business">
    <h2 class="heading heading--xl">About<br>the business</h2>
    <p class="body-copy">At Brel Fosk Painting, we strive to provide a high quality service and exceptional craftsmanship to all our clients, and continue to find new and better ways to care for your home and the environment.</p>
    <p class="body-copy">We take the time to research alternative eco painting products and processes. We can also provide you with information about the products and why we use them, so you feel confident in every choice.</p>
    <p class="body-copy">We aim to limit the interruption to clients and their families as a result of our work. Safety is paramount, and we make sure that you are satisfied with the work done.</p>
    <p class="body-copy">Brel Fosk Painting is dedicated to learning, understanding and implementing new products and techniques that will be safer for the environment and your family. All this is done at a competitive price.</p>
  </div>

  <div class="panel panel--professional">
    <h2 class="heading heading--xl">Hiring a<br>professional</h2>
    <p class="body-copy">Hiring a professional painter is never an easy decision and your risk is to take the cheapest quote. Hiring a highly skilled trade will bring considered experience and expertise to deliver a high quality finish.</p>
  </div>

  <div class="panel panel--green">
    <h2 class="heading heading--xl">Going<br>green</h2>
    <p class="body-copy">We can help you make smart decisions about creating a better environment and a better home for your family and the world we live in. This can be achieved by reducing the amount of VOCs in the organic compounds used to colour and protect your home.</p>
  </div>
</section>

</body>
</html>
```